Halvik - consultancy website

I need a new design for my webpage/presence [to be functioning with Wordpress - I have a programmer to set it up but not the design idea].
My company is Halvik - a consultancy firm focused on growth management for Swedish SME's primarily;. We call it Leadership toolkit for firms on the rise, kind of a doctor helping small become big. Contentwise, its a simple frontpage + 3-4 subpages with content re company/myself/focus etc. The new site should communicate a fresh, trustworthy take yet simple and functional on all devices [i.e. think UI compatible for mobile/tablet]. Current building parts/form elements are
a) existing logo and text elements
b) existing pictures
c) the yellowish color
colours and new ideas on pictures/positioning are welcome. I prefer a 'full width page' solution with centralised text elements but that's all up to you to suggest. Current site is a quickfix made by myself - now I'm moving it to a new platform so want to take the opportunity to make it
Nothing superspecial as it is a 2-man show; on the other hand I still want to have a modern & fresh reflection of my brand in digital environments. Help me out!
www.halvik-demo.se
Best
Lina Bergqvist

```html
<!DOCTYPE html>
<html lang="en">
<head>
<meta charset="utf-8">
<title>Halvik – About us</title>
<link href="https://fonts.googleapis.com/css2?family=Alegreya:wght@400;700&family=Open+Sans:ital,wght@0,400;0,600;0,700;1,400&display=swap" rel="stylesheet">
<style>
:root{
  --orange:#ec8a2c;
  --orange-dark:#d9781c;
  --ink:#2b2b2b;
  --text:#666;
  --band:#f3f3f3;
  --footer:#3b3b3b;
  --footer-bottom:#333;
  --footer-text:#ddd;
  --white:#fff;
  --serif:'Alegreya',Georgia,serif;
  --sans:'Open Sans',Arial,sans-serif;
}
*{box-sizing:border-box;margin:0;padding:0}
html,body{width:723px;height:1200px;overflow:hidden;background:var(--white)}
.page{position:relative;width:723px;height:1200px;font-family:var(--sans);color:var(--text)}
.abs{position:absolute}

/* header */
.brand{left:56px;top:16px;font-family:var(--serif);font-size:30px;color:var(--ink);line-height:1}
.tagline{left:60px;top:45px;font-family:var(--serif);font-size:10px;color:var(--ink)}
.search{left:490px;top:27px;width:174px;height:25px;border:1px solid #ccc;border-radius:2px;font-size:8px;color:#999;padding:7px 10px}
.search svg{position:absolute;right:10px;top:7px}

/* nav */
.nav{left:0;top:75px;width:723px;height:32px;background:var(--orange);display:flex;justify-content:center}
.nav ul{list-style:none;display:flex;margin-left:-2px}
.nav li{width:101px;height:32px;line-height:32px;text-align:center;font-family:var(--serif);font-size:8.5px;font-weight:700;color:var(--white);border-left:1px solid var(--orange-dark)}
.nav li:first-child{border-left:none}

/* hero */
.hero{left:0;top:107px;width:723px;height:250px;background:linear-gradient(180deg,#8ea3b6 0%,#6d8298 45%,#566a7c 80%,#7c93a6 100%)}
.hero h1{position:absolute;width:100%;top:105px;text-align:center;font-family:var(--serif);font-size:36px;font-weight:700;color:var(--white)}
.hero .arrow{position:absolute;top:115px}

/* about */
.section-title{left:60px;top:376px;font-family:var(--serif);font-size:17px;font-weight:700;color:var(--ink)}
.about-photo{left:59px;top:414px;width:200px;height:233px;border:1px solid #ddd;background:linear-gradient(180deg,#f2f2f2 0%,#eceae8 60%,#e4c7a6 100%)}
.about-text{left:277px;top:410px;width:390px;font-size:7.2px;line-height:15.6px}
.about-text p{margin-bottom:15.6px}
.read-more{left:276px;top:638px;font-size:7.5px;font-weight:700;color:var(--orange)}

/* team */
.team{left:0;top:674px;width:723px;height:215px;background:var(--band)}
.team h2{position:absolute;width:100%;top:18px;text-align:center;font-family:var(--serif);font-size:15px;font-weight:700;color:var(--ink)}
.member{position:absolute;top:59px;width:110px;text-align:center}
.member .avatar{width:93px;height:93px;border-radius:50%;margin:0 auto;background:linear-gradient(160deg,#c9d3dd,#5a6574)}
.member .name{margin-top:9px;font-family:var(--serif);font-size:10.5px;color:var(--ink)}
.member .role{margin-top:2px;font-family:var(--serif);font-style:italic;font-size:8px;color:var(--orange)}

/* testimonials */
.testimonials{left:0;top:889px;width:723px;height:138px;background:var(--orange);color:var(--white);text-align:center}
.testimonials h2{position:absolute;width:100%;top:13px;font-family:var(--serif);font-size:15px;font-weight:700}
.quote{position:absolute;left:120px;width:483px;top:48px;font-style:italic;font-size:7.2px;line-height:15.5px}
.quote b{font-family:var(--serif);font-size:11px;font-style:normal}
.author{position:absolute;width:100%;top:88px;font-size:9px}
.author-role{position:absolute;width:100%;top:108px;font-size:7.2px;font-style:italic}
.testimonials .arrow{position:absolute;top:62px}

/* footer */
.footer{left:0;top:1027px;width:723px;height:135px;background:var(--footer);color:var(--footer-text)}
.footer h3{font-family:var(--serif);font-size:9.5px;font-weight:700;color:var(--white);margin-bottom:12px}
.footer .col{position:absolute;top:20px;font-size:7.2px;line-height:13px}
.footer .divider{position:absolute;top:18px;width:1px;height:100px;background:#474747}
.email-field{width:206px;height:19px;background:#555;margin-top:10px;color:#aaa;font-size:7px;padding:5px 7px}
.subscribe{display:inline-block;margin-top:11px;background:var(--orange);color:var(--white);font-size:7px;font-weight:700;padding:5px 8px;border-radius:2px}
.contact-row{display:flex;gap:14px;margin-bottom:10px}
.contact-row svg{flex:none;margin-top:1px}
.footer-bottom{left:0;top:1162px;width:723px;height:38px;background:var(--footer-bottom);border-top:1px solid #2c2c2c;color:var(--footer-text);font-size:7.2px}
.copy{position:absolute;left:59px;top:13px}
.social{position:absolute;right:61px;top:12px;display:flex;gap:11px}
.social span{width:12px;height:12px;background:#eee;border-radius:2px}
</style>
</head>
<body>
<div class="page">

  <div class="abs brand">Halvik.</div>
  <div class="abs tagline">Leadership toolkit for firms on the rise</div>
  <div class="abs search">Search...
    <svg width="10" height="10" viewBox="0 0 10 10"><circle cx="4" cy="4" r="3" fill="none" stroke="#888" stroke-width="1.4"/><line x1="6.2" y1="6.2" x2="9" y2="9" stroke="#888" stroke-width="1.6"/></svg>
  </div>

  <nav class="abs nav">
    <ul>
      <li>Home</li><li>About us</li><li>What we Do</li><li>Who We Are</li><li>Why Halvik</li><li>Contact us</li>
    </ul>
  </nav>

  <section class="abs hero" role="img" aria-label="City skyline across a harbour under a pale sky">
    <svg class="arrow" style="left:20px" width="14" height="22" viewBox="0 0 14 22"><polyline points="11,2 3,11 11,20" fill="none" stroke="#fff" stroke-width="2.5"/></svg>
    <h1>About us</h1>
    <svg class="arrow" style="right:20px" width="14" height="22" viewBox="0 0 14 22"><polyline points="3,2 11,11 3,20" fill="none" stroke="#fff" stroke-width="2.5"/></svg>
  </section>

  <h2 class="abs section-title">A Few Word About us</h2>
  <div class="abs about-photo" role="img" aria-label="Child looking up beside height marks on a white wall"></div>
  <div class="abs about-text">
    <p>Independent consulting across several diciplines, supporting businesses influenced by a ‘fast forward’ mindset and desire to optimize its operations.With a background in Marketing and Economics,&nbsp; I’ve spent the past 10 years in the exiting space where Telecom &amp; IT meets fashion industry.</p>
    <p>Several managing roles in Global Operations and&nbsp; Business transformation have set me up with a broad range of competencies and a truly global profile.I practise PMQ based standards, securing deliverables along the way through simple applications and process flows.</p>
    <p>Actually, many businesses don’t.Many business leaders instead feel uneasy when thinking about the Big Picture; the company’s strategic framework.&nbsp; Or how it is relayed internally to employees.</p>
    <p>The list of complex issues in need of attention keeps growing but simply not enough time. As everyday business need to be prioritized to stay ahead, it can certainly be a hardship to even identify, yet perform the structural improvements needed to mature with your industry.</p>
  </div>
  <div class="abs read-more">READ MORE &gt;&gt;</div>

  <section class="abs team">
    <h2>Our Team</h2>
    <div class="member" style="left:53px"><div class="avatar" role="img" aria-label="Portrait of team member"></div><div class="name">Anders Holm</div><div class="role">( Manager )</div></div>
    <div class="member" style="left:179px"><div class="avatar" role="img" aria-label="Portrait of team member"></div><div class="name">Sofia</div><div class="role">( Manager )</div></div>
    <div class="member" style="left:306px"><div class="avatar" role="img" aria-label="Portrait of team member"></div><div class="name">Mikael</div><div class="role">( Manager )</div></div>
    <div class="member" style="left:433px"><div class="avatar" role="img" aria-label="Portrait of team member"></div><div class="name">Elin</div><div class="role">( Manager )</div></div>
    <div class="member" style="left:560px"><div class="avatar" role="img" aria-label="Portrait of team member"></div><div class="name">Oskar</div><div class="role">( Manager )</div></div>
  </section>

  <section class="abs testimonials">
    <h2>Testimonials</h2>
    <svg class="arrow" style="left:54px" width="9" height="14" viewBox="0 0 9 14"><polyline points="7,1 2,7 7,13" fill="none" stroke="#fff" stroke-width="2"/></svg>
    <p class="quote"><b>“</b>&nbsp; Important deliverables under Lina’s responsibility has involved not only the creation of many successful creative product strategies, but also constructing efficient process flows and forming organizational structures to meet with market developments. &nbsp;<b>”</b></p>
    <div class="author">- Per Sandgren</div>
    <div class="author-role">( Former CEO of Norvik Group )</div>
    <svg class="arrow" style="right:54px" width="9" height="14" viewBox="0 0 9 14"><polyline points="2,1 7,7 2,13" fill="none" stroke="#fff" stroke-width="2"/></svg>
  </section>

  <footer class="abs footer">
    <div class="col" style="left:59px;width:140px">
      <h3>About us</h3>
      The Halvik properties are described as remarkably robust, delivering seamless entanglement across any partition and acting as a sophisticated enabler when applied into operations.
    </div>
    <div class="divider" style="left:218px"></div>
    <div class="col" style="left:245px;width:210px">
      <h3>Newsletter Subscription</h3>
      Register Your Email Address To get Information About us
      <div class="email-field">Email Address</div>
      <span class="subscribe">SUBSCRIBE</span>
    </div>
    <div class="divider" style="left:477px"></div>
    <div class="col" style="left:507px;width:160px">
      <h3>Contact Us</h3>
      <div class="contact-row">
        <svg width="7" height="10" viewBox="0 0 7 10"><path d="M3.5 0A3.3 3.3 0 0 0 .2 3.3C.2 5.8 3.5 10 3.5 10S6.8 5.8 6.8 3.3A3.3 3.3 0 0 0 3.5 0z" fill="#eee"/><circle cx="3.5" cy="3.3" r="1.2" fill="#3b3b3b"/></svg>
        <span>Kungsgatan 18, floor 3, 111 35 Stockholm, Sweden</span>
      </div>
      <div class="contact-row">
        <svg width="10" height="10" viewBox="0 0 10 10"><path d="M2 0.5l2 2.2-1 1.3c.6 1.3 1.7 2.4 3 3l1.3-1 2.2 2-1.2 1.6C4.6 9.4.6 5.4.4 1.7z" fill="#eee"/></svg>
        <span>+46 [0] 700 12 34 56</span>
      </div>
      <div class="contact-row">
        <svg width="11" height="8" viewBox="0 0 11 8"><rect width="11" height="8" rx="1" fill="#eee"/><polyline points="0.5,0.8 5.5,4.6 10.5,0.8" fill="none" stroke="#3b3b3b" stroke-width="1"/></svg>
        <span style="text-decoration:underline">info@halvik-demo.se</span>
      </div>
    </div>
  </footer>

  <div class="abs footer-bottom">
    <div class="copy">Copyrights © Halvik 2015 . All rights Reserved.</div>
    <div class="social" aria-label="Social links"><span></span><span></span><span></span><span></span><span></span></div>
  </div>

</div>
</body>
</html>
```